Capability Statement Flyer

We want to develop a flyer to show potential clients our work capability. We want to incorporate our logo. You can reference our website for any other graphics you may want to incorporate. Our blue CMYK is 100-80-0-22

Industry/Entity Type

Work

Colors
0555a3

Requirements
Must have
• Capability Statement
• Our expertise and technical resources fuel the delivery of our services. As a leading provider of construction services, Halvern Construction focuses on providing solutions for civil infrastructure, industrial infrastructure, and commercial market segments. Driven by a commitment to continuous improvement, Halvern Construction has the expertise in the following key areas:
• • Design Build/Problem Solving
• • Storm and Process Water Systems
• • Heavy and Structural Concrete
• • Bridge Construction
• • Building Construction and Restoration
• • Hardscapes
• • All Civil Construction and Utility
Nice to have
• Creativity to present to potential clients. Not just words on the page

```html
<!DOCTYPE html>
<html lang="en">
<head>
<meta charset="utf-8">
<title>Halvern Construction – Capability Flyer</title>
<link href="https://fonts.googleapis.com/css2?family=Lato:wght@400;700&family=Oswald:wght@500;700&display=swap" rel="stylesheet">
<style>
  :root{
    --brand-blue:#1f3a9e;
    --brand-blue-bright:#3b63d6;
    --brand-navy:#13287a;
    --card-dark:#3d3d3d;
    --footer-dark:#3a3a3a;
    --paper:#f4f4f4;
    --paper-shade:#e6e6e6;
    --ink:#2a2a2a;
    --stage:#8c8c8c;
  }
  *{box-sizing:border-box;margin:0;padding:0}
  html,body{width:1200px;height:1200px;overflow:hidden;background:var(--stage)}
  .flyer{
    position:absolute;left:187px;top:20px;width:826px;height:1160px;
    background:linear-gradient(180deg,var(--paper) 0%,var(--paper-shade) 55%,var(--paper) 100%);
    font-family:"Lato",sans-serif;color:var(--ink);overflow:hidden;
  }
  .hero{position:absolute;left:0;top:0}
  .logo-block{
    position:absolute;left:329px;top:262px;width:167px;height:166px;
    background:#fff;border:3px solid #8a8a8a;
    display:flex;flex-direction:column;align-items:center;justify-content:center;gap:10px;
  }
  .logo-block .mark{width:70px;height:70px;background:var(--brand-blue)}
  .logo-block .name{
    font-family:"Oswald",sans-serif;font-weight:700;color:var(--brand-blue);
    font-size:21px;line-height:1.05;text-align:center;letter-spacing:.5px;text-transform:uppercase;
  }
  .card{
    position:absolute;top:503px;width:216px;height:185px;background:var(--card-dark);color:#fff;
    padding:10px 13px 0;text-align:center;
  }
  .card::before,.card::after{content:"";position:absolute;border:3px solid var(--brand-blue)}
  .card::before{left:-8px;top:-8px;width:62px;height:52px;border-right:none;border-bottom:none}
  .card::after{right:-8px;bottom:-8px;width:62px;height:52px;border-left:none;border-top:none}
  .card.civil{left:44px}.card.industrial{left:306px}.card.commercial{left:566px}
  .card .icon{display:block;width:36px;height:36px;margin:4px auto 6px;background:#fff;opacity:.9;border-radius:3px}
  .card h2{font-family:"Oswald",sans-serif;font-weight:700;font-size:18px;letter-spacing:.2px;margin-bottom:6px}
  .card p{font-size:10px;line-height:1.32;text-align:justify;text-align-last:center}
  .intro{position:absolute;left:34px;width:760px;font-size:13px;line-height:1.25}
  .intro.one{top:726px}.intro.two{top:777px}
  .service{position:absolute;width:200px;margin-left:-100px;text-align:center}
  .service .badge{display:block;width:77px;height:77px;margin:0 auto 10px;border-radius:50%;background:var(--brand-blue);border:2px solid #fff;box-shadow:0 0 0 1px var(--brand-blue)}
  .service span{font-weight:700;font-size:15.5px;line-height:1.25;color:#333}
  .footer{position:absolute;left:0;top:1084px}
  .contact{position:absolute;left:36px;top:1095px;color:#fff}
  .contact div{display:flex;align-items:center;gap:10px}
  .contact .phone{font-size:19px;font-weight:700}
  .contact .addr{font-size:13px;margin-top:4px}
  .social{position:absolute;top:1112px;color:#fff;font-size:12.5px;display:flex;align-items:center;gap:7px}
  .social i{display:inline-block;width:10px;height:10px;border-radius:50%;background:#fff}
</style>
</head>
<body>
<main class="flyer">
  <svg class="hero" width="826" height="480" viewBox="0 0 826 480">
    <defs>
      <linearGradient id="photoTone" x1="0" y1="0" x2="0" y2="1">
        <stop offset="0" stop-color="#c9d8e6"/>
        <stop offset=".35" stop-color="#d9d6cf"/>
        <stop offset=".7" stop-color="#8d8378"/>
        <stop offset="1" stop-color="#6f7a55"/>
      </linearGradient>
      <linearGradient id="bandL" x1="0" y1="0" x2="1" y2="0">
        <stop offset="0" stop-color="var(--brand-navy)"/><stop offset="1" stop-color="var(--brand-blue-bright)"/>
      </linearGradient>
      <linearGradient id="bandR" x1="1" y1="0" x2="0" y2="0">
        <stop offset="0" stop-color="var(--brand-navy)"/><stop offset="1" stop-color="var(--brand-blue-bright)"/>
      </linearGradient>
    </defs>
    <rect width="826" height="470" fill="url(#photoTone)" role="img" aria-label="Photograph of a brick office building with white columns and large black-framed windows"/>
    <polygon points="0,298 412,420 412,470 0,355" fill="url(#bandL)"/>
    <polygon points="826,238 412,420 412,470 826,292" fill="url(#bandR)"/>
    <polygon points="260,310 412,360 570,330 570,420 412,470 260,420" fill="var(--brand-blue)"/>
    <polygon points="0,355 412,470 826,292 826,480 0,480" fill="var(--paper)"/>
  </svg>

  <div class="logo-block">
    <span class="mark"></span>
    <span class="name">Halvern<br>Construction</span>
  </div>

  <section class="card civil">
    <span class="icon" role="img" aria-label="Engineer with hard hat icon"></span>
    <h2>CIVIL PROJECTS</h2>
    <p>Halvern Construction focuses in all phases of civil infrastructure enhancement including site preparation, concrete foundations and paving, storm water systems, structural retaining walls as well as heavy and structural concrete.</p>
  </section>
  <section class="card industrial">
    <span class="icon" role="img" aria-label="Factory icon"></span>
    <h2>INDUSTRIAL PROJECTS</h2>
    <p>Utilizing the highest safety standards, Halvern Construction focuses on plant facility water systems, heavy concrete, facility repair and upgrades. Industrial focus industries include chemical, railways, energy and manufacturing.</p>
  </section>
  <section class="card commercial">
    <span class="icon" role="img" aria-label="Office buildings icon"></span>
    <h2>COMMERCIAL PROJECTS</h2>
    <p>Halvern Construction provides commercial general contracting, design build, project management, problem solving and more.</p>
  </section>

  <p class="intro one">Our expertise and technical resources fuel the delivery of our services. As a leading provider of construction services, Halvern Construction focuses on providing solutions for civil infrastructure, industrial infrastructure, and commercial market segments.</p>
  <p class="intro two">Driven by a commitment to continuous improvement, Halvern Construction has the expertise in the following key areas:</p>

  <div class="service" style="left:117px;top:800px"><span class="badge" role="img" aria-label="Hammer and pencil icon"></span><span>Design Build/<br>Problem Solving</span></div>
  <div class="service" style="left:314px;top:800px"><span class="badge" role="img" aria-label="Water outflow icon"></span><span>Storm and Process<br>Water Systems</span></div>
  <div class="service" style="left:517px;top:800px"><span class="badge" role="img" aria-label="Concrete mixer truck icon"></span><span>Heavy and<br>Structural Concrete</span></div>
  <div class="service" style="left:709px;top:800px"><span class="badge" role="img" aria-label="Suspension bridge icon"></span><span>Bridge<br>Construction</span></div>
  <div class="service" style="left:213px;top:940px"><span class="badge" role="img" aria-label="Tower crane and building icon"></span><span>Building Construction<br>and Restoration</span></div>
  <div class="service" style="left:404px;top:940px"><span class="badge" role="img" aria-label="Brick wall icon"></span><span>Hardscapes</span></div>
  <div class="service" style="left:609px;top:940px"><span class="badge" role="img" aria-label="Hard hat and gear icon"></span><span>All Civil Construction<br>and Utility</span></div>

  <svg class="footer" width="826" height="76" viewBox="0 0 826 76">
    <polygon points="0,0 384,0 400,76 0,76" fill="var(--brand-blue)"/>
    <polygon points="418,0 826,0 826,76 434,76" fill="var(--footer-dark)"/>
  </svg>
  <div class="contact">
    <div class="phone">
      <svg width="14" height="12" viewBox="0 0 14 12"><path d="M1 4c3-4 9-4 12 0l-2 2-2-1V3H5v2L3 6z M3 7h8l1 5H2z" fill="#fff"/></svg>
      +612 85550192
    </div>
    <div class="addr">
      <svg width="12" height="14" viewBox="0 0 12 14"><path d="M6 0a5 5 0 0 1 5 5c0 4-5 9-5 9S1 9 1 5a5 5 0 0 1 5-5z" fill="#fff"/><circle cx="6" cy="5" r="2" fill="var(--brand-blue)"/></svg>
      27 Wattle Bay Road, Kirrawee Sydney NSW 2232
    </div>
  </div>
  <div class="social" style="left:478px"><i></i>/halvernconstruction</div>
  <div class="social" style="left:652px"><i></i>/halvernconstruction</div>
</main>
</body>
</html>
```